Vernac Law Business cards and stationary design project

We are looking for a stationary design for business cards (double sided), 8x10, 5x7, and legal and standard envelopes.

We would like the design to match the logo that we have already.
Color palate preferred is Teal, White, grey and any others that will look good for a professional law firm.

We would like this statement: "RELATIONSHIPS. RESPECT. RESULT" to be on the back of the business cards and maybe on the stationary if it looks good.

Please see link to website for more information: www.vernac-law.example

Target Market(s)

Potential clients that need Attorney services.

Industry/Entity Type

Law Firm

Contact Information for Business Card

We would like the front and back to be two different colors. Current business cards are teal front, grey back and are a vertical design. We are open to options with colors.

Font styles to use
Serif

Colors
33a6d7
33b8a4
b9b9b9
5c5c5c

Requirements
Must have
• Logo supplied needs to go on the card and stationary.
• Match website color palate, www.vernac-law.example
• Be professional and not too wordy.
• Criminal Law, Civil Litigation, Personal Injury, Restraining Orders need to be on the card.
Nice to have
• RELATIONSHIPS. RESPECT. RESULTS. on the back of the card.
Should not have
• Not be too busy/wordy or too flashy.

```html
<!DOCTYPE html>
<html lang="en">
<head>
<meta charset="utf-8">
<title>Vernac Law – Business Card</title>
<link href="https://fonts.googleapis.com/css2?family=Cinzel:wght@400;600&family=Open+Sans:wght@400;600&display=swap" rel="stylesheet">
<style>
  :root {
    --teal: #2fa9b8;
    --teal-soft: #3bb3c0;
    --charcoal: #4a4b4d;
    --charcoal-deep: #3c3d3f;
    --grey-band: #5c5c5c;
    --paper: #fbfbfb;
    --ink: #2a2a2a;
    --light-text: #e6e6e6;
    --backdrop: #e8e6e3;
  }
  * { box-sizing: border-box; margin: 0; padding: 0; }
  html, body {
    width: 1200px; height: 800px; overflow: hidden;
    background: var(--backdrop);
  }
  .canvas {
    position: relative; width: 1200px; height: 800px;
    display: flex; align-items: center; justify-content: center; gap: 50px;
  }
  .card {
    position: relative; width: 530px; height: 303px;
    box-shadow: 0 8px 24px rgba(0,0,0,.18);
    overflow: hidden;
  }

  /* ---------- Firm name (plain text) ---------- */
  .firm-name {
    font-family: "Open Sans", sans-serif; font-weight: 600;
    line-height: 1; white-space: nowrap;
  }

  /* ---------- Back side ---------- */
  .card-back {
    background: linear-gradient(160deg, var(--charcoal) 0%, var(--charcoal-deep) 100%);
    color: var(--light-text);
  }
  .card-back .firm-name {
    position: absolute; top: 44px; right: 40px;
    font-size: 30px; color: var(--teal-soft);
  }
  .card-back .rule {
    position: absolute; left: 40px; right: 40px; height: 2px; background: var(--teal);
  }
  .card-back .rule.top { top: 112px; }
  .card-back .rule.bottom { top: 170px; left: 120px; }
  .tagline {
    position: absolute; top: 124px; left: 40px; right: 40px; text-align: right;
    font-family: "Cinzel", serif; font-size: 24px; color: #f2f2f2; letter-spacing: .5px;
    white-space: nowrap;
  }
  .practice {
    position: absolute; right: 40px; bottom: 26px; list-style: none; text-align: right;
    font-family: "Open Sans", sans-serif; font-size: 12.5px; line-height: 1.6; color: var(--light-text);
  }
  .practice li::after {
    content: ""; display: inline-block; width: 6px; height: 6px; border-radius: 50%;
    background: var(--teal-soft); margin-left: 8px; vertical-align: middle;
  }

  /* ---------- Front side ---------- */
  .card-front { background: var(--paper); }
  .edge-band {
    position: absolute; left: 0; top: 0; bottom: 0; width: 26px;
    background: linear-gradient(to bottom, var(--teal) 0 62%, var(--grey-band) 62% 100%);
  }
  .card-front .firm-name {
    position: absolute; left: 46px; top: 122px; width: 220px; text-align: center;
    font-size: 26px; color: var(--teal);
  }
  .divider {
    position: absolute; left: 282px; top: 38px; width: 1.5px; height: 150px; background: var(--teal);
  }
  .contact {
    position: absolute; left: 298px; top: 40px;
    font-family: "Open Sans", sans-serif; color: var(--ink);
  }
  .person {
    font-family: "Cinzel", serif; font-weight: 600; color: var(--teal);
    font-size: 20px; letter-spacing: 1px;
  }
  .role { font-size: 10px; letter-spacing: .5px; margin: 2px 0 14px; }
  .lines { list-style: none; font-size: 13px; line-height: 1.55; }
  .lines .key { color: var(--teal); font-weight: 600; margin-right: 6px; }
  .address { font-size: 13px; line-height: 1.45; margin-top: 12px; }
</style>
</head>
<body>
<main class="canvas">

  <section class="card card-back" aria-label="Business card, back">
    <div class="firm-name">Vernac Law</div>
    <div class="rule top"></div>
    <p class="tagline">Relationships. Respect. Results.</p>
    <div class="rule bottom"></div>
    <ul class="practice">
      <li>Practice areas</li>
      <li>Criminal Law</li>
      <li>Restraining Orders</li>
      <li>Civil Litigation/Personal Injury</li>
    </ul>
  </section>

  <section class="card card-front" aria-label="Business card, front">
    <div class="edge-band"></div>
    <div class="firm-name">Vernac Law</div>
    <div class="divider"></div>
    <div class="contact">
      <div class="person">Claire Dumont</div>
      <div class="role">LAWYER</div>
      <ul class="lines">
        <li><span class="key">[P]</span>(555) 014-2780</li>
        <li><span class="key">[E]</span>claire@vernac-law.example</li>
        <li><span class="key">[W]</span>www.vernac-law.example</li>
      </ul>
      <p class="address">418 Harbor View Rd. #200<br>Bayside, CA 90000</p>
    </div>
  </section>

</main>
</body>
</html>
```